Im open to ideas.. I was thinking on my business cards aswell as my logo. a place for my name. email. phone number and abn..

ive attched a file with my business logo. which i dont love the colours.. i was think a dark background with charcoal letters so something along those colour schumes but im open to ideas..

BRM Constructions

```html
<!DOCTYPE html>
<html lang="en">
<head>
<meta charset="UTF-8">
<title>BRM Constructions — Business Card</title>
<link href="https://fonts.googleapis.com/css2?family=Open+Sans:wght@400;600;700&display=swap" rel="stylesheet">
<style>
  :root {
    --backdrop-top: #cfcfcf;
    --backdrop-bottom: #ffffff;
    --card: #1b1b1b;
    --card-edge: #2a2a2a;
    --wordmark-muted: #8d8d8d;
    --wordmark-bright: #ffffff;
    --name: #d6d6d6;
    --detail: #bdbdbd;
    --icon: #a9a9a9;
  }
  * { box-sizing: border-box; margin: 0; padding: 0; }
  html, body { width: 1200px; height: 900px; overflow: hidden; }
  body {
    position: relative;
    background: linear-gradient(to bottom, var(--backdrop-top) 0%, #e4e4e4 55%, var(--backdrop-bottom) 100%);
    font-family: "Open Sans", Arial, sans-serif;
  }
  .card {
    position: absolute;
    top: 307px;
    width: 438px;
    height: 270px;
    background: var(--card);
    border: 1px solid var(--card-edge);
    border-radius: 12px;
  }
  .card--back { left: 149px; }
  .card--front { left: 609px; }

  .wordmark {
    position: absolute;
    font-weight: 600;
    line-height: 1;
    white-space: nowrap;
    text-align: center;
  }
  .card--back .wordmark {
    left: 36px;
    top: 130px;
    width: 180px;
    font-size: 19px;
    color: var(--wordmark-muted);
  }
  .card--front .wordmark {
    left: 0;
    top: 115px;
    width: 100%;
    font-size: 40px;
    color: var(--wordmark-bright);
  }

  .contact {
    position: absolute;
    left: 247px;
    top: 71px;
    color: var(--detail);
  }
  .contact__name { font-size: 14.5px; font-weight: 600; color: var(--name); line-height: 18px; }
  .contact__role { font-size: 12px; line-height: 15px; }
  .contact__abn { font-size: 12px; margin-top: 18px; line-height: 15px; }
  .contact__abn b { font-weight: 700; }
  .contact__list { list-style: none; margin-top: 14px; }
  .contact__list li {
    display: flex;
    align-items: center;
    gap: 7px;
    font-size: 12px;
    line-height: 16px;
  }
  .contact__list svg { width: 9px; height: 9px; fill: var(--icon); flex: none; }
</style>
</head>
<body>
  <section class="card card--back" aria-label="Card back with contact details">
    <div class="wordmark">BRM Constructions</div>
    <div class="contact">
      <p class="contact__name">Daniel Harper</p>
      <p class="contact__role">Managing Director</p>
      <p class="contact__abn"><b>ABN :</b> 12398745</p>
      <ul class="contact__list">
        <li>
          <svg viewBox="0 0 10 10" aria-hidden="true"><path d="M2.2 0.6 3.6 2.6 2.7 3.6C3.3 5 4.9 6.7 6.4 7.3L7.4 6.4 9.4 7.8 8.6 9.4C4.6 9.3 0.7 5.4 0.6 1.4Z"/></svg>
          044-987 654 321
        </li>
        <li>
          <svg viewBox="0 0 10 10" aria-hidden="true"><path d="M0.5 2h9v6h-9z M0.9 2.4 5 5.6 9.1 2.4" fill="none" stroke="#a9a9a9" stroke-width="1.1"/></svg>
          hello@brmbuild.com
        </li>
        <li>
          <svg viewBox="0 0 10 10" aria-hidden="true"><circle cx="5" cy="5" r="4.5"/><path d="M0.8 5h8.4M5 0.6c-2 2.5-2 6.3 0 8.8M5 0.6c2 2.5 2 6.3 0 8.8" stroke="#1b1b1b" stroke-width="0.8" fill="none"/></svg>
          www.brmbuild.com
        </li>
      </ul>
    </div>
  </section>

  <section class="card card--front" aria-label="Card front">
    <div class="wordmark">BRM Constructions</div>
  </section>
</body>
</html>
```